Child sleep consultant needs a flyer to attract new clients

We need a flyer that will attract the attention of parents with children between newborn and 3 years old who may be experiencing sleep issues. The flyer will be placed at places such as community centres, doctors room, play centres, etc.

Our business is called Drowsy Tiny Folk and provides a sleep consultancy service. Our service essentially provides a routine for parents to follow and general advice. Our service is not medical advice.

We need the flyer to have an overall tone that is soft and peaceful however can catch the attention of parents who may be struggling on minimal sleep. We would like photos with minimal text. The colour we use is green.

We will provide the text to appear in the flyer once we have a better idea of the layout that we prefer for the flyer. The text however wont be extensive, just some catchy points.

We want to direct people to our website which is drowsytinyfolk.com.au. We also have a facebook page, which is Drowsy Tiny Folk.

We have a logo that we would like to appear on the flyer. We will attach the file once the uploader on pixel bazaar is fixed.

Our consultant is a certified Rest Wise consultant, which has a separate logo that should appear somewhere on the logo. I will attach this once the uploader is fixed.

When we print the flyer - we want to print A5 SIZE ... please make sure the formatting is OK for this size.

Target Market(s)

Mums and Dads with children between newborn and 3 years old.

Industry/Entity Type

Consultant

Colors
cadf82

Requirements
Must have
• - Our logo.
• - Rest Wise consultant logo - both attached to this brief.
• - Contact details - including phone number, email address and website
• - MUST be suitable for A5 printable size, double sided please.
• Must have the following text:
• If your baby or toddler isn't sleeping through the night, neither are you - and this means you are probably feeling physically and mentally exhausted, stressed, depressed and irritable, afraid you might be damaging your child and disconnected from your partner.
• The good news is nearly all healthy children 3 months or older are physically capable of sleeping 12 solid hours without waking. They just need to be taught the healthy sleep habits that enable them to do so.
• I can help with the sleep issues your child is experiencing. As a certified Rest Wise (insert trademark TM here) I can help if:
• - your child will only fall asleep when nursing or bottle feeding
• - your child needs a dummy in order fall asleep
• - you're waking up with your child one or more times per night
• - your child needs to be rocked, patted, or taken for a car ride to go to sleep
• - your own lack of sleep is starting to take a toll on your family
• I've been personally trained by Mara Felgate, best selling author of the Rest Wise (insert trade mark symbol here) Program to teach her sleep training methods to families like yours. Mara's methods have already helped over 30,000 parents and children and I'd be delighted to help your family next!
• Call or email for a free 15 minute consultation
• I would love to connect with you to talk about your child's specific situation and discuss different solutions.

```html
<!DOCTYPE html>
<html lang="en">
<head>
<meta charset="utf-8">
<title>Drowsy Tiny Folk – A5 Flyer</title>
<link href="https://fonts.googleapis.com/css2?family=Pathway+Gothic+One&family=Patrick+Hand&display=swap" rel="stylesheet">
<style>
  :root{
    --bg:#e6e6e6;
    --paper:#ffffff;
    --green:#82ae78;
    --green-dark:#5f8f55;
    --lime:#cadf82;
    --lime-soft:#dfeab4;
    --photo-top:#f3f2ef;
    --photo-bottom:#e6d6c8;
  }
  *{box-sizing:border-box;margin:0;padding:0}
  html,body{width:1200px;height:960px;overflow:hidden;background:var(--bg)}
  .canvas{position:relative;width:1200px;height:960px}
  .page{position:absolute;top:112px;width:517px;height:734px;background:var(--paper);overflow:hidden}
  .page--front{left:58px}
  .page--back{left:623px}
  .page-art{position:absolute;inset:0}
  .caps{font-family:"Pathway Gothic One",sans-serif;letter-spacing:.2px}
  .hand{font-family:"Patrick Hand",cursive}
  .abs{position:absolute}

  /* brand mark */
  .brand{position:absolute;display:flex;align-items:center;gap:10px}
  .brand-dot{width:34px;height:34px;border-radius:50%;background:var(--lime)}
  .brand-name{font-family:"Patrick Hand",cursive;color:var(--green-dark);font-size:32px;line-height:.95}

  /* front */
  .headline{left:290px;top:38px;width:210px;color:var(--green-dark);font-size:29px;line-height:1.12}
  .headline span{display:block}
  .cta{left:48px;top:412px;width:210px;text-align:center;color:#fff;font-size:23px;line-height:1.15}
  .intro{left:30px;top:518px;width:458px;text-align:center;color:#555;font-size:12.6px;line-height:1.45}
  .tagline{left:0;width:517px;top:632px;text-align:center;color:var(--green);font-size:24px}
  .front-contact{left:0;width:517px;top:674px;text-align:center;color:var(--green);font-size:23px}
  .front-contact .sep{color:var(--lime);margin:0 4px}

  /* back */
  .intro-caps{left:0;width:517px;top:46px;text-align:center;color:#fff;font-size:22px;line-height:1.3}
  .points{left:10px;top:140px;width:497px;display:flex;justify-content:space-between;list-style:none}
  .points li{width:92px;text-align:center;color:#fff;font-size:14.5px;line-height:1.42}
  .trained{left:20px;top:312px;width:477px;text-align:center;color:#fff;font-size:14px;line-height:1.55}
  .helped{left:250px;top:374px;width:240px;text-align:center;color:#fff;font-size:19px;line-height:1.2}
  .connect{left:20px;top:504px;width:477px;text-align:center;color:var(--green-dark);font-size:22px;line-height:1.35}
  .web{left:244px;top:584px;width:242px;height:34px;display:flex;align-items:center;justify-content:center;color:var(--green-dark);font-size:17px}
  .back-contact{left:250px;top:626px;width:230px;text-align:center;color:var(--green-dark);font-size:17.5px;line-height:1.6}
</style>
</head>
<body>
<div class="canvas">

  <!-- FRONT -->
  <section class="page page--front">
    <svg class="page-art" viewBox="0 0 517 734" width="517" height="734">
      <defs>
        <linearGradient id="photoTone" x1="0" y1="0" x2="0" y2="1">
          <stop offset="0" stop-color="var(--photo-top)"/>
          <stop offset=".55" stop-color="#ede4dc"/>
          <stop offset="1" stop-color="var(--photo-bottom)"/>
        </linearGradient>
      </defs>
      <path role="img" aria-label="Photo of a crying baby lying on a white pillow beside a teddy bear"
        fill="url(#photoTone)"
        d="M250 0 H517 V470 C500 495 460 505 430 495 C400 515 350 512 320 500 L110 470 C60 455 20 430 0 400 V230
           C40 240 90 230 110 200 C160 210 220 185 240 140 C280 130 300 90 290 50 C285 25 268 6 250 0 Z"/>
      <g fill="var(--green)">
        <path d="M60 400 C60 370 100 360 118 378 C130 348 180 345 196 372 C220 360 255 378 250 405
                 C275 410 285 440 265 460 C280 485 255 510 225 505 L80 505 C50 505 35 478 50 460 C30 445 40 410 60 400 Z"/>
      </g>
      <g fill="var(--lime)">
        <polygon points="108,392 111,400 119,400 113,405 115,413 108,408 101,413 103,405 97,400 105,400"/>
        <polygon points="126,402 128,406 132,406 129,409 130,413 126,411 122,413 123,409 120,406 124,406"/>
      </g>
    </svg>

    <div class="brand" style="left:28px;top:70px">
      <span class="brand-dot"></span>
      <span class="brand-name">Drowsy<br>Tiny<br>Folk</span>
    </div>

    <h1 class="abs headline hand">
      <span>We help families</span>
      <span style="padding-left:30px">and their little ones</span>
      <span>to get the sleep</span>
      <span style="padding-left:74px">they need.</span>
    </h1>

    <p class="abs cta caps">CALL OR EMAIL FOR<br>A FREE 15 MINUTE<br>CONSULTATION</p>

    <p class="abs intro hand">If your baby or toddler isn't sleeping through the night, neither are you - and this means you are probably feeling physically and mentally exhausted, stressed, depressed and irritable, afraid you might be damaging your child and disconnected from your partner. The good news is nearly all healthy children 3 months or older are physically capable of sleeping 12 solid hours without waking. They just need to be taught the healthy sleep habits that enable them to do so.</p>

    <p class="abs tagline caps">YOUR LITTLE PERSON IS NEVER TOO YOUNG TO START</p>
    <p class="abs front-contact hand">E: nell@drowsytinyfolk.com.au <span class="sep">★</span> P: 0491 570 156</p>
  </section>

  <!-- BACK -->
  <section class="page page--back">
    <svg class="page-art" viewBox="0 0 517 734" width="517" height="734">
      <path fill="var(--green)"
        d="M0 0 H517 V480 C500 500 440 505 400 492 C350 505 290 495 270 470 C250 440 230 420 210 420
           C200 390 160 375 130 390 C105 375 60 385 55 410 C40 400 28 360 25 320 C22 305 12 298 0 296 Z"/>
      <path d="M0 228 C60 240 120 270 170 280 C230 292 300 270 360 262 C420 258 470 270 517 310"
        fill="none" stroke="#fff" stroke-width="1.3" stroke-dasharray="5 5" opacity=".9"/>
      <circle cx="120" cy="280" r="16" fill="none" stroke="#fff" stroke-width="1.3" stroke-dasharray="5 5"/>
      <circle cx="290" cy="276" r="9" fill="none" stroke="#fff" stroke-width="1.3" stroke-dasharray="4 4"/>
      <!-- certification badge -->
      <path fill="#fff" stroke="var(--lime)" stroke-width="1.5"
        d="M60 420 C60 400 90 392 105 405 C115 385 150 385 160 408 C180 405 195 425 185 445
           C195 460 180 475 165 472 L62 472 C42 472 35 450 48 440 C38 432 45 418 60 420 Z"/>
      <rect role="img" aria-label="Certified Rest Wise consultant badge" x="84" y="418" width="72" height="36" rx="8" fill="var(--lime-soft)"/>
      <g fill="var(--lime)">
        <polygon points="192,470 196,480 207,480 198,486 201,496 192,490 183,496 186,486 177,480 188,480"/>
        <polygon points="212,484 214,489 219,489 215,492 216,497 212,494 208,497 209,492 205,489 210,489"/>
        <path d="M222 460 C214 452 214 442 222 442 C226 442 229 446 229 446 C229 446 232 442 236 442 C244 442 244 452 236 460 L229 468 Z" transform="rotate(-15 229 455)"/>
        <polygon points="574,0 0,0" />
        <polygon points="446,560 448,565 453,565 449,568 450,573 446,570 442,573 443,568 439,565 444,565"/>
      </g>
      <!-- web ribbon -->
      <path fill="var(--lime-soft)" d="M244 584 H486 L476 601 L486 618 H244 L252 601 Z"/>
      <g fill="var(--lime)">
        <polygon points="82,115 85,122 92,122 86,126 88,133 82,129 76,133 78,126 72,122 79,122"/>
        <polygon points="173,115 176,122 183,122 177,126 179,133 173,129 167,133 169,126 163,122 170,122"/>
        <polygon points="263,115 266,122 273,122 267,126 269,133 263,129 257,133 259,126 253,122 260,122"/>
        <polygon points="353,115 356,122 363,122 357,126 359,133 353,129 347,133 349,126 343,122 350,122"/>
        <polygon points="443,115 446,122 453,122 447,126 449,133 443,129 437,133 439,126 433,122 440,122"/>
      </g>
    </svg>

    <h2 class="abs intro-caps caps">I CAN HELP WITH THE SLEEP ISSUES YOUR CHILD IS EXPERIENCING.<br>AS A CERTIFIED REST WISE™ I CAN HELP IF:</h2>

    <ul class="abs points hand">
      <li>your child will only fall asleep when nursing or bottle feeding</li>
      <li>your child needs a dummy in order fall asleep</li>
      <li>you're waking up with your child one or more times per night</li>
      <li>your child needs to be rocked, patted, or taken for a car ride to go to sleep</li>
      <li>your own lack of sleep is starting to take a toll on your family</li>
    </ul>

    <p class="abs trained hand">I've been personally trained by Mara Felgate, best selling author of<br>the Rest Wise™ Program to teach her sleep training methods to families like yours.</p>

    <p class="abs helped caps">MARA'S METHODS HAVE ALREADY HELPED OVER 30,000 PARENTS AND CHILDREN AND I'D BE DELIGHTED TO HELP YOUR FAMILY NEXT!</p>

    <p class="abs connect hand">I would love to connect with you to talk about your child's<br>specific situation and discuss different solutions.</p>

    <div class="brand" style="left:40px;top:610px">
      <span class="brand-dot"></span>
      <span class="brand-name">Drowsy<br>Tiny<br>Folk</span>
    </div>

    <p class="abs web hand">www.drowsytinyfolk.com.au</p>
    <p class="abs back-contact hand">E: nell@drowsytinyfolk.com.au<br>P: 0491 570 156<br>facebook.com/drowsytinyfolk</p>
  </section>

</div>
</body>
</html>
```